TalkHarbor - Language Coaching Services

Sleek, innovative, trendy design for Language Coaching business.

TalkHarbor is a new UK based company that provides Language Coaching services. We offer highly personalized on-line and face to face language courses. We also impart learning techniques workshops based on the latest neuroscience research for second-language acquisition.

Target Market(s)

See attached info

Industry/Entity Type

Consulting

Contact Information for Business Card

TalkHarbor
DaniaKV@talkharbor.co.uk
TalkHarbor.co.uk
London, UK

Font styles to use
Sans Serif

```html
<!DOCTYPE html>
<html lang="en">
<head>
<meta charset="utf-8">
<title>TalkHarbor Business Card</title>
<link rel="stylesheet" href="https://fonts.googleapis.com/css2?family=Montserrat:wght@400&family=Roboto:wght@400;700&display=swap">
<style>
  :root {
    --stage: #2b2b2d;
    --card-dark: #1d1d1f;
    --brand-blue: #0a7bb3;
    --brand-blue-bright: #1a8fd0;
    --white: #ffffff;
    --ink: #333333;
    --muted: #8a8a8a;
  }
  * { margin: 0; padding: 0; box-sizing: border-box; }
  html, body { width: 1200px; height: 960px; overflow: hidden; }
  body {
    background: var(--stage);
    font-family: "Roboto", Arial, sans-serif;
    position: relative;
  }
  .card {
    position: absolute;
    left: 240px;
    width: 720px;
    height: 411px;
    border-radius: 4px;
    overflow: hidden;
  }
  /* Back side */
  .card-back { top: 46px; background: var(--card-dark); }
  .back-mark {
    position: absolute;
    left: 0; right: 0; top: 120px;
    display: flex; align-items: center; justify-content: center; gap: 26px;
  }
  .back-ring {
    width: 130px; height: 130px; border-radius: 50%;
    border: 12px solid var(--brand-blue-bright);
  }
  .back-name {
    font-family: "Montserrat", Arial, sans-serif;
    font-weight: 400;
    font-size: 46px;
    letter-spacing: 2px;
    color: var(--brand-blue-bright);
  }
  .back-web {
    position: absolute; left: 0; right: 0; top: 300px;
    text-align: center;
    color: var(--white);
    font-size: 17px;
    letter-spacing: 4px;
  }
  /* Front side */
  .card-front { top: 503px; background: var(--white); }
  .front-field {
    position: absolute; left: 0; top: 0;
    width: 420px; height: 100%;
    background: var(--brand-blue);
  }
  .front-brand {
    position: absolute; left: 62px; top: 56px;
    display: flex; flex-direction: column; align-items: flex-start; gap: 16px;
  }
  .brand-dot {
    width: 76px; height: 76px; border-radius: 50%;
    border: 8px solid var(--white);
    margin-left: 56px;
  }
  .brand-name {
    font-family: "Montserrat", Arial, sans-serif;
    font-weight: 400;
    font-size: 38px;
    letter-spacing: 1px;
    color: var(--white);
  }
  .contact {
    position: absolute; right: 34px; top: 168px;
    text-align: right;
  }
  .contact-name {
    color: var(--brand-blue);
    font-weight: 700;
    font-size: 25px;
    letter-spacing: 0.5px;
  }
  .contact-role {
    color: var(--muted);
    font-size: 16px;
    margin-bottom: 20px;
  }
  .contact-line {
    display: flex; justify-content: flex-end; align-items: center; gap: 10px;
    color: var(--ink);
    font-size: 17px;
    line-height: 27px;
  }
  .contact-icon { width: 16px; height: 16px; fill: var(--brand-blue); }
</style>
</head>
<body>

<section class="card card-back" aria-label="Card back">
  <div class="back-mark">
    <div class="back-ring"></div>
    <div class="back-name">TalkHarbor</div>
  </div>
  <div class="back-web">talkharbor.co.uk</div>
</section>

<section class="card card-front" aria-label="Card front">
  <div class="front-field" role="img" aria-label="Large blue silhouette illustration area"></div>

  <div class="front-brand">
    <div class="brand-dot"></div>
    <div class="brand-name">TALKHARBOR</div>
  </div>

  <div class="contact">
    <div class="contact-name">OWEN MARLOW</div>
    <div class="contact-role">CEO/FOUNDER</div>
    <div class="contact-line">
      <span>689 555 0142</span>
      <svg class="contact-icon" viewBox="0 0 16 16" aria-hidden="true"><path d="M4 0h8a1.5 1.5 0 0 1 1.5 1.5v13A1.5 1.5 0 0 1 12 16H4a1.5 1.5 0 0 1-1.5-1.5v-13A1.5 1.5 0 0 1 4 0zm0 2v10.5h8V2zm4 11.3a.9.9 0 1 0 0 1.8.9.9 0 0 0 0-1.8z"/></svg>
    </div>
    <div class="contact-line">
      <span>info@talkharbor.co.uk</span>
      <svg class="contact-icon" viewBox="0 0 16 16" aria-hidden="true"><path d="M0 3h16v10H0zm1.6 1.2L8 9l6.4-4.8z"/></svg>
    </div>
    <div class="contact-line">
      <span>talkharbor.co.uk</span>
      <svg class="contact-icon" viewBox="0 0 16 16" aria-hidden="true"><circle cx="8" cy="8" r="7.5"/><path d="M1 8h14M8 .5c-3 3-3 12 0 15M8 .5c3 3 3 12 0 15" stroke="#fff" stroke-width="1" fill="none"/></svg>
    </div>
  </div>
</section>

</body>
</html>
```